QuillVane needs a dashboard page designed

Redesign the dashboard shown in the provided images.

There are two images:
- dashboard.png
- dashboard-expanded.png

NOTE: The vocabulary navigation on the left will be a very long list of words 100s, so keep that in mind when you're designing both the vocab navigation and the expanded vocab popup.

In the dashboard.png picture, there needs to be a progress chart showing the word progress like the following: review 1(show it as completed) -> review 2(show the user they are here) -> review 3(unvisited) -> review 4(unvisited)

The do-not-design-this-page.png image is for your reference only. It is not to be designed. Use it to understand the overall look and feel of the website to help you create the best dashboard page possible.
Updates

Need extra days to review

Industry/Entity Type

Education English learning

Number of Pages Required

1 page

Requirements
Must have
• The main navigation and main header cannot change between pages. See the do-not-design page for the main navigateion and header.
Should not have
• Do not add a person profile. We will not have images of our users. Keep the icons in the main navigation as they are.

```html
<!DOCTYPE html>
<html lang="en">
<head>
<meta charset="utf-8">
<title>LexiPath Tutor – Vocabulary Dashboard</title>
<link href="https://fonts.googleapis.com/css2?family=Lato:wght@300;400;700;900&display=swap" rel="stylesheet">
<style>
:root{
  --page:#e9edf5;
  --white:#ffffff;
  --rail:#2c343d;
  --rail-top:#262d35;
  --rail-active:#3c4551;
  --brand:#2d62ad;
  --ink:#1f2328;
  --muted:#8a8f96;
  --soft:#e6e6e6;
  --step-off:#9b9b9b;
  --gold:#f2b705;
  --online:#3cc35a;
  --scrim:rgba(0,0,0,.46);
}
*{margin:0;padding:0;box-sizing:border-box}
html,body{width:977px;height:1200px;overflow:hidden}
body{background:var(--page);font-family:'Lato',sans-serif;color:var(--ink);position:relative}
.screen{position:absolute;left:67.5px;width:839px;height:510.5px;background:var(--white);overflow:hidden;box-shadow:0 6px 24px rgba(40,60,100,.08)}
.screen--default{top:61.3px}
.screen--expanded{top:628px}
.abs{position:absolute}
.ico{display:inline-block;vertical-align:middle}

/* main rail */
.rail{left:19.7px;top:13.5px;width:60px;height:469.5px;background:var(--rail);border-radius:11px 0 0 11px}
.rail__head{height:42px;background:var(--rail-top);border-radius:11px 0 0 0}
.rail__item{position:absolute;left:0;width:54px;text-align:center;color:var(--white);font-size:6px;line-height:8px}
.rail__item svg{display:block;margin:0 auto 3px}
.rail__item--active{background:var(--rail-active);height:39px;top:42px;padding-top:9px}

/* vocab nav */
.vocab{left:73.7px;top:13.5px;width:132px;height:469.5px;background:var(--white);border-radius:0 11px 11px 0;box-shadow:4px 0 14px rgba(0,0,0,.06)}
.select{position:absolute;border:1px solid #d5d8dc;border-radius:4px;background:var(--white);font-size:6px;padding-left:6px;display:flex;align-items:center;justify-content:space-between;padding-right:5px}
.vocab .select{left:5.5px;top:11.5px;width:48.5px;height:17px}
.expand{position:absolute;left:85px;top:14px;color:var(--brand);font-size:7.3px;display:flex;align-items:center;gap:4px}
.group{position:absolute;left:13px;font-size:7.8px;display:flex;align-items:center;gap:5px;white-space:nowrap}
.current{position:absolute;color:var(--brand);font-weight:700}
.vocab .current{left:12.3px;top:62px;font-size:8.2px}
.words{position:absolute;list-style:none;color:var(--muted);font-weight:300}
.vocab .words{left:25.3px;font-size:5.6px;line-height:12.1px}

/* header */
.topbar{left:206px;top:18px;width:615.7px;height:37px;background:var(--brand);border-radius:0 11px 11px 0}
.topbar__title{position:absolute;left:0;right:0;top:10px;text-align:center;color:var(--white);font-size:12.4px;font-weight:400;letter-spacing:.2px}
.topbar__gear{left:537px;top:13.5px}
.topbar__user{left:561px;top:13.5px}
.avatar{left:583.5px;top:7.8px;width:21.4px;height:21.4px;border-radius:50%;background:linear-gradient(160deg,#b9c3cc,#6b5a4d);border:1.5px solid var(--white)}
.avatar__dot{left:582.5px;top:7px;width:5px;height:5px;border-radius:50%;background:var(--online)}

/* content */
.word-title{left:223.4px;top:74px;font-size:12px;font-weight:700}
.stars{left:258px;top:75.5px;color:var(--gold);font-size:10px;letter-spacing:-.5px}
.cta{left:694px;top:70px;width:128px;height:26.5px;background:var(--rail);border-radius:14px;color:var(--white);font-size:6px;font-weight:900;display:flex;align-items:center;justify-content:center;gap:5px}

.track{position:absolute;top:125px;height:2px}
.track--done{left:237.5px;width:365.5px;background:var(--brand)}
.track--todo{left:603px;width:176.5px;background:var(--soft)}
.step{position:absolute;top:112px;width:28px;height:28px;margin-left:-14px;border-radius:50%;color:var(--white);font-size:11px;display:flex;align-items:center;justify-content:center}
.step--done,.step--here{background:var(--brand);font-weight:700}
.step--here{box-shadow:0 0 0 2px var(--white),0 0 0 3px var(--brand)}
.step--next{background:var(--step-off);font-weight:400}
.step-label{position:absolute;top:145px;font-size:6px;font-weight:700;color:var(--brand);transform:translateX(-50%);white-space:nowrap}
.step-label--next{color:var(--step-off)}

.prose{position:absolute;left:224px;font-size:7.55px;line-height:14.9px;white-space:nowrap}
.prose--word{top:168.5px}
.prose--analysis{top:424.5px}
.section-title{position:absolute;font-size:9px;font-weight:700}
.section-title--curve{left:233px;top:242px}
.section-title--analysis{left:223px;top:406px}
.chart{left:232.4px;top:259.5px}

/* expanded state */
.scrim{inset:0;background:var(--scrim)}
.modal{left:281px;top:63px;width:434.5px;height:237.5px;background:var(--white);border-radius:11px}
.modal .select{left:15.8px;top:18px;width:58.5px;height:21.4px;font-size:7px}
.modal .group{font-size:9.6px;gap:7px}
.modal .current{left:16.6px;top:78.5px;font-size:10px}
.modal .words{font-size:7.3px;line-height:14.9px}
</style>
</head>
<body>

<svg width="0" height="0" style="position:absolute" aria-hidden="true">
  <defs>
    <symbol id="i-home" viewBox="0 0 16 16"><path d="M8 2 1 8h2v6h4v-4h2v4h4V8h2z" fill="currentColor"/></symbol>
    <symbol id="i-map" viewBox="0 0 16 16"><path d="M1 5l4-2 4 2v9l-4-2-4 2zM10 7l1 .5V14l3-1.5V8" fill="currentColor"/><circle cx="12.5" cy="3.5" r="2.3" fill="none" stroke="currentColor" stroke-width="1.3"/></symbol>
    <symbol id="i-case" viewBox="0 0 16 16"><path d="M6 3h4v2h4v9H2V5h4zM7 4v1h2V4z" fill="currentColor" fill-rule="evenodd"/><rect x="2" y="8.5" width="12" height="1" fill="#2c343d"/></symbol>
    <symbol id="i-clock" viewBox="0 0 16 16"><circle cx="8" cy="8" r="6" fill="none" stroke="currentColor" stroke-width="1.8"/><path d="M8 4.5V8l2.5 1.5" fill="none" stroke="currentColor" stroke-width="1.6"/></symbol>
    <symbol id="i-move" viewBox="0 0 16 16"><path d="M8 1 5.5 3.5h5zM8 15l-2.5-2.5h5zM1 8l2.5-2.5v5zM15 8l-2.5 2.5v-5z" fill="currentColor"/><circle cx="8" cy="8" r="2.6" fill="none" stroke="currentColor" stroke-width="1.5"/></symbol>
    <symbol id="i-lock" viewBox="0 0 16 16"><rect x="3" y="7" width="10" height="8" rx="1.5" fill="none" stroke="currentColor" stroke-width="1.5"/><path d="M5 7V4.8a3 3 0 0 1 6 0V7" fill="none" stroke="currentColor" stroke-width="1.5"/><rect x="7.3" y="9.5" width="1.4" height="3" fill="currentColor"/></symbol>
    <symbol id="i-help" viewBox="0 0 16 16"><circle cx="8" cy="8" r="6.5" fill="none" stroke="currentColor" stroke-width="1.4"/><path d="M6 6.2a2 2 0 1 1 2.6 1.9c-.5.2-.6.5-.6 1.2" fill="none" stroke="currentColor" stroke-width="1.4"/><circle cx="8" cy="11.6" r=".9" fill="currentColor"/></symbol>
    <symbol id="i-open" viewBox="0 0 16 16"><path d="M9 2h5v5M14 2 7.5 8.5M12 9.5V14H2V4h4.5" fill="none" stroke="currentColor" stroke-width="1.5"/></symbol>
    <symbol id="i-chev" viewBox="0 0 10 10"><path d="M2.5 3.5 5 6l2.5-2.5" fill="none" stroke="currentColor" stroke-width="1.4"/></symbol>
    <symbol id="i-gear" viewBox="0 0 16 16"><path d="M7 1h2l.4 2 1.4.6 1.7-1.2 1.4 1.4-1.2 1.7.6 1.4 2 .4v2l-2 .4-.6 1.4 1.2 1.7-1.4 1.4-1.7-1.2-1.4.6L9 15H7l-.4-2-1.4-.6-1.7 1.2-1.4-1.4 1.2-1.7L2.7 9 1 9V7l2-.4.6-1.4-1.2-1.7 1.4-1.4 1.7 1.2 1.4-.6z" fill="currentColor"/><circle cx="8" cy="8" r="2.2" fill="#2d62ad"/></symbol>
    <symbol id="i-user" viewBox="0 0 16 16"><circle cx="8" cy="4.5" r="3.2" fill="currentColor"/><path d="M2 15c0-4 2.6-6 6-6s6 2 6 6z" fill="currentColor"/></symbol>

    <symbol id="curve-chart" viewBox="533 570 1040 230">
      <rect x="533" y="576" width="1033" height="46" fill="#e8eef7"/>
      <rect x="533" y="622" width="1033" height="90" fill="#eaf4ea"/>
      <rect x="533" y="712" width="1033" height="23" fill="#fdfbe6"/>
      <rect x="533" y="735" width="1033" height="23" fill="#f1f1f1"/>
      <g font-family="Lato, sans-serif" font-size="9.5" fill="#6d7279">
        <text x="545" y="600">Long-Term Memory</text>
        <text x="545" y="667">Working Memory</text>
        <text x="545" y="723">Short-Term Memory</text>
        <text x="545" y="745">Forgotten Memory</text>
      </g>
      <rect x="627" y="718" width="18" height="40" fill="#2d62ad"/>
      <rect x="730" y="622" width="18" height="136" fill="#2d62ad"/>
      <path d="M650 713C690 718 715 735 728 748" fill="none" stroke="#444" stroke-width="1.3" stroke-dasharray="1.5 3"/>
      <path d="M748 622C830 630 860 635 900 690C925 725 935 740 945 755" fill="none" stroke="#444" stroke-width="1.3" stroke-dasharray="1.5 3"/>
      <g font-family="Lato, sans-serif" font-size="9" font-weight="700" fill="#1f2328">
        <rect x="598" y="699" width="52" height="19" rx="3" fill="#fff" stroke="#d9dce0"/>
        <text x="624" y="712" text-anchor="middle">May 18</text>
        <rect x="690" y="608" width="51" height="19" rx="3" fill="#fff" stroke="#d9dce0"/>
        <text x="715.5" y="621" text-anchor="middle">May 19</text>
      </g>
      <line x1="533" y1="758" x2="1568" y2="758" stroke="#333" stroke-width="1.2"/>
      <g stroke="#333" stroke-width="1">
        <line x1="545" y1="758" x2="545" y2="764"/><line x1="596" y1="758" x2="596" y2="764"/>
        <line x1="648" y1="758" x2="648" y2="764"/><line x1="700" y1="758" x2="700" y2="764"/>
        <line x1="751" y1="758" x2="751" y2="764"/><line x1="803" y1="758" x2="803" y2="764"/>
        <line x1="854" y1="758" x2="854" y2="764"/><line x1="906" y1="758" x2="906" y2="764"/>
        <line x1="957" y1="758" x2="957" y2="764"/><line x1="1009" y1="758" x2="1009" y2="764"/>
        <line x1="1060" y1="758" x2="1060" y2="764"/><line x1="1112" y1="758" x2="1112" y2="764"/>
        <line x1="1163" y1="758" x2="1163" y2="764"/><line x1="1215" y1="758" x2="1215" y2="764"/>
        <line x1="1266" y1="758" x2="1266" y2="764"/><line x1="1318" y1="758" x2="1318" y2="764"/>
        <line x1="1369" y1="758" x2="1369" y2="764"/><line x1="1421" y1="758" x2="1421" y2="764"/>
        <line x1="1472" y1="758" x2="1472" y2="764"/><line x1="1524" y1="758" x2="1524" y2="764"/>
      </g>
      <g font-family="Lato, sans-serif" font-size="10" fill="#1f2328" text-anchor="middle">
        <text x="548" y="779">18 May</text><text x="596" y="779">12:00</text>
        <text x="648" y="779">19 May</text><text x="700" y="779">12:00</text>
        <text x="751" y="779">20 May</text><text x="803" y="779">12:00</text>
        <text x="854" y="779">21 May</text><text x="906" y="779">12:00</text>
        <text x="957" y="779">22 May</text><text x="1009" y="779">12:00</text>
        <text x="1060" y="779">23 May</text><text x="1112" y="779">12:00</text>
        <text x="1163" y="779">24 May</text><text x="1215" y="779">12:00</text>
        <text x="1266" y="779">25 May</text><text x="1318" y="779">12:00</text>
        <text x="1369" y="779">26 May</text><text x="1421" y="779">12:00</text>
        <text x="1472" y="779">27 May</text><text x="1524" y="779">12:00</text>
        <text x="1560" y="779">28 .</text>
        <text x="1054" y="793" font-weight="700">Date Range</text>
      </g>
    </symbol>
  </defs>
</svg>

<!-- ============ Dashboard ============ -->
<section class="screen screen--default">
  <nav class="rail abs">
    <div class="rail__head"></div>
    <div class="rail__item rail__item--active"><svg width="10" height="10"><use href="#i-home"/></svg>LexiPath Tutor</div>
    <div class="rail__item" style="top:100px"><svg width="11" height="11"><use href="#i-map"/></svg>Daily English</div>
    <div class="rail__item" style="top:145px"><svg width="11" height="11"><use href="#i-case"/></svg>Business</div>
  </nav>

  <aside class="vocab abs">
    <div class="select">All <svg width="6" height="6"><use href="#i-chev"/></svg></div>
    <div class="expand">Expand <svg width="8" height="8"><use href="#i-open"/></svg></div>
    <div class="group" style="top:43px;left:12px"><svg width="7" height="7"><use href="#i-clock"/></svg>Short-Term Memory <svg width="6" height="6"><use href="#i-help"/></svg></div>
    <div class="current">Grap</div>
    <div class="group" style="top:83px;left:12px"><svg width="7" height="7"><use href="#i-move"/></svg>Working Memory <svg width="6" height="6"><use href="#i-help"/></svg></div>
    <ul class="words" style="top:98.5px">
      <li>Cool Down</li><li>Crave</li><li>Go For</li><li>Go-To</li><li>In The Mood For</li><li>Sip</li><li>Soothing</li><li>Stick With</li><li>Throw In/Throw On</li>
    </ul>
    <div class="group" style="top:220px;left:12px"><svg width="7" height="7"><use href="#i-lock"/></svg>Long-Term Memory <svg width="6" height="6"><use href="#i-help"/></svg></div>
    <ul class="words" style="top:237.5px"><li>Give It A Try</li></ul>
  </aside>

  <header class="topbar abs">
    <div class="topbar__title">LexiPath Tutor ▾</div>
    <svg class="topbar__gear abs" width="10" height="10" style="color:#fff"><use href="#i-gear"/></svg>
    <svg class="topbar__user abs" width="10" height="10" style="color:#fff"><use href="#i-user"/></svg>
    <div class="avatar abs" role="img" aria-label="Signed-in learner avatar"></div>
    <div class="avatar__dot abs"></div>
  </header>

  <h1 class="word-title abs">Grap</h1>
  <div class="stars abs">★★★★★</div>
  <div class="cta abs"><svg width="5" height="5" viewBox="0 0 10 10"><path d="M1 0l9 5-9 5z" fill="#fff"/></svg>Start Vocabulary Review Exercise 3</div>

  <div class="track track--done"></div>
  <div class="track track--todo"></div>
  <div class="step step--done" style="left:237.5px">01</div>
  <div class="step step--here" style="left:417px">02</div>
  <div class="step step--next" style="left:603px">03</div>
  <div class="step step--next" style="left:779.5px">04</div>
  <div class="step-label" style="left:237px">Review 1</div>
  <div class="step-label" style="left:418px">Review 2</div>
  <div class="step-label step-label--next" style="left:602px">Review 3</div>
  <div class="step-label step-label--next" style="left:781px">Review 4</div>

  <p class="prose prose--word">The word "<b>grab</b>" is most commonly used as a verb, meaning to take something quickly or suddenly. Imagine you're running late for school. You don't have time for breakfast,<br>so you quickly grab an apple from the kitchen and rush out the door. As you reach the bus stop, your friend waves and says, "Hey! Let's grab a coffee after class." Later, when<br>you sit down, your phone starts ringing. You grab it from your bag and answer.</p>

  <h2 class="section-title section-title--curve">Learning Curve Graph</h2>
  <svg class="chart abs" width="585" height="129.4"><use href="#curve-chart"/></svg>

  <h2 class="section-title section-title--analysis">LexiPath Tutor Learning Analysis</h2>
  <p class="prose prose--analysis">Lorem ipsum dolor sit amet, consectetur adipiscing elit. Nam rutrum commodo enim id bibendum. Nunc dignissim risus erat, nec finibus nunc dictum eu. Aliquam sit amet<br>euismod metus, quis malesuada erat. Sed at felis quis nulla feugiat cursus at at dolor. Maecenas pretium aliquet dapibus. Fusce et eleifend massa. Sed convallis ex mi, at<br>lobortis ligula congue vel. Pellentesque pharetra molestie leo, sed vehicula felis commodo molestie. Aliquam dapibus ultrices efficitur. Duis porta mauris eros. at tempus sem</p>
</section>

<!-- ============ Dashboard with expanded vocabulary ============ -->
<section class="screen screen--expanded">
  <nav class="rail abs">
    <div class="rail__head"></div>
    <div class="rail__item rail__item--active"><svg width="10" height="10"><use href="#i-home"/></svg>LexiPath Tutor</div>
    <div class="rail__item" style="top:100px"><svg width="11" height="11"><use href="#i-map"/></svg>Daily English</div>
    <div class="rail__item" style="top:145px"><svg width="11" height="11"><use href="#i-case"/></svg>Business</div>
  </nav>

  <aside class="vocab abs">
    <div class="select">All <svg width="6" height="6"><use href="#i-chev"/></svg></div>
    <div class="expand">Expand <svg width="8" height="8"><use href="#i-open"/></svg></div>
    <div class="group" style="top:43px;left:12px"><svg width="7" height="7"><use href="#i-clock"/></svg>Short-Term Memory <svg width="6" height="6"><use href="#i-help"/></svg></div>
    <div class="current">Grap</div>
    <div class="group" style="top:83px;left:12px"><svg width="7" height="7"><use href="#i-move"/></svg>Working Memory <svg width="6" height="6"><use href="#i-help"/></svg></div>
    <ul class="words" style="top:98.5px">
      <li>Cool Down</li><li>Crave</li><li>Go For</li><li>Go-To</li><li>In The Mood For</li><li>Sip</li><li>Soothing</li><li>Stick With</li><li>Throw In/Throw On</li>
    </ul>
    <div class="group" style="top:220px;left:12px"><svg width="7" height="7"><use href="#i-lock"/></svg>Long-Term Memory <svg width="6" height="6"><use href="#i-help"/></svg></div>
    <ul class="words" style="top:237.5px"><li>Give It A Try</li></ul>
  </aside>

  <header class="topbar abs">
    <div class="topbar__title">LexiPath Tutor ▾</div>
    <svg class="topbar__gear abs" width="10" height="10" style="color:#fff"><use href="#i-gear"/></svg>
    <svg class="topbar__user abs" width="10" height="10" style="color:#fff"><use href="#i-user"/></svg>
    <div class="avatar abs" role="img" aria-label="Signed-in learner avatar"></div>
    <div class="avatar__dot abs"></div>
  </header>

  <h1 class="word-title abs">Grap</h1>
  <div class="stars abs">★★★★★</div>
  <div class="cta abs"><svg width="5" height="5" viewBox="0 0 10 10"><path d="M1 0l9 5-9 5z" fill="#fff"/></svg>Start Vocabulary Review Exercise 3</div>

  <div class="track track--done"></div>
  <div class="track track--todo"></div>
  <div class="step step--done" style="left:237.5px">01</div>
  <div class="step step--here" style="left:417px">02</div>
  <div class="step step--next" style="left:603px">03</div>
  <div class="step step--next" style="left:779.5px">04</div>
  <div class="step-label" style="left:237px">Review 1</div>
  <div class="step-label" style="left:418px">Review 2</div>
  <div class="step-label step-label--next" style="left:602px">Review 3</div>
  <div class="step-label step-label--next" style="left:781px">Review 4</div>

  <p class="prose prose--word">The word "<b>grab</b>" is most commonly used as a verb, meaning to take something quickly or suddenly. Imagine you're running late for school. You don't have time for breakfast,<br>so you quickly grab an apple from the kitchen and rush out the door. As you reach the bus stop, your friend waves and says, "Hey! Let's grab a coffee after class." Later, when<br>you sit down, your phone starts ringing. You grab it from your bag and answer.</p>

  <h2 class="section-title section-title--curve">Learning Curve Graph</h2>
  <svg class="chart abs" width="585" height="129.4"><use href="#curve-chart"/></svg>

  <h2 class="section-title section-title--analysis">LexiPath Tutor Learning Analysis</h2>
  <p class="prose prose--analysis">Lorem ipsum dolor sit amet, consectetur adipiscing elit. Nam rutrum commodo enim id bibendum. Nunc dignissim risus erat, nec finibus nunc dictum eu. Aliquam sit amet<br>euismod metus, quis malesuada erat. Sed at felis quis nulla feugiat cursus at at dolor. Maecenas pretium aliquet dapibus. Fusce et eleifend massa. Sed convallis ex mi, at<br>lobortis ligula congue vel. Pellentesque pharetra molestie leo, sed vehicula felis commodo molestie. Aliquam dapibus ultrices efficitur. Duis porta mauris eros. at tempus sem</p>

  <div class="scrim abs"></div>

  <div class="modal abs" role="dialog" aria-label="All vocabulary">
    <div class="select">All <svg width="7" height="7"><use href="#i-chev"/></svg></div>
    <div class="group" style="left:16px;top:56px"><svg width="9" height="9"><use href="#i-clock"/></svg>Short-Term Memory <svg width="7" height="7"><use href="#i-help"/></svg></div>
    <div class="current">Grap</div>
    <div class="group" style="left:160px;top:56px"><svg width="9" height="9"><use href="#i-move"/></svg>Working Memory <svg width="7" height="7"><use href="#i-help"/></svg></div>
    <ul class="words" style="left:176.7px;top:74px">
      <li>Cool Down</li><li>Crave</li><li>Go For</li><li>Go-To</li><li>In The Mood For</li><li>Sip</li><li>Soothing</li><li>Stick With</li><li>Throw In/Throw On</li>
    </ul>
    <div class="group" style="left:303px;top:54px"><svg width="9" height="9"><use href="#i-lock"/></svg>Long-Term Memory <svg width="7" height="7"><use href="#i-help"/></svg></div>
    <ul class="words" style="left:319px;top:74.5px"><li>Give It A Try</li></ul>
  </div>
</section>

</body>
</html>
```